Business Card Design Project

Looking to update our business cards. We have a logo with our slogan. We are an IT firm so we wouldlike a modern look.

Industry/Entity Type

Business

```html
<!DOCTYPE html>
<html lang="en">
<head>
<meta charset="utf-8">
<title>Kernelworks Business Card</title>
<link rel="stylesheet" href="https://fonts.googleapis.com/css2?family=Jost:wght@400;500;600&display=swap">
<style>
  :root {
    --olive: #6b7f3a;
    --olive-deep: #5e7132;
    --lime: #a9c23f;
    --ink: #222222;
    --paper: #ffffff;
    --backdrop: #ecebe7;
  }
  html, body {
    margin: 0;
    padding: 0;
    width: 1200px;
    height: 699px;
    overflow: hidden;
    background: var(--backdrop);
    font-family: "Jost", sans-serif;
  }
  .canvas {
    position: relative;
    width: 1200px;
    height: 699px;
  }
  .card {
    position: absolute;
    top: 200px;
    width: 525px;
    height: 300px;
    border-radius: 22px;
    overflow: hidden;
    box-shadow: 0 6px 18px rgba(0,0,0,0.18);
  }
  .card-front { left: 55px; background: var(--paper); }
  .card-back { left: 620px; background: var(--olive); }

  .brand {
    position: absolute;
    left: 0;
    right: 0;
    text-align: center;
  }
  .brand-name {
    display: inline-flex;
    align-items: center;
    gap: 10px;
    font-weight: 500;
    letter-spacing: 0.14em;
    line-height: 1;
  }
  .brand-dot {
    display: inline-block;
    border-radius: 50%;
  }
  .brand-slogan {
    font-weight: 600;
    letter-spacing: 0.22em;
    text-transform: uppercase;
  }

  .card-front .brand { top: 32px; }
  .card-front .brand-name { font-size: 40px; color: var(--olive); }
  .card-front .brand-dot { width: 13px; height: 13px; background: var(--olive); }
  .card-front .brand-slogan { margin-top: 10px; font-size: 12px; color: var(--ink); }

  .address {
    position: absolute;
    top: 122px;
    left: 0;
    right: 0;
    margin: 0;
    text-align: center;
    font-size: 14px;
    color: var(--ink);
    letter-spacing: 0.02em;
  }

  .front-band {
    position: absolute;
    left: 0;
    right: 0;
    bottom: 0;
    height: 78px;
    background: linear-gradient(180deg, var(--olive) 0%, var(--olive-deep) 100%);
    border-top: 4px solid var(--lime);
  }
  .front-band::before {
    content: "";
    position: absolute;
    left: 0;
    right: 0;
    top: -10px;
    height: 3px;
    background: var(--ink);
  }

  .contacts {
    position: absolute;
    right: 24px;
    top: 148px;
    list-style: none;
    margin: 0;
    padding: 0;
    font-size: 12.5px;
    color: var(--ink);
    line-height: 17px;
  }
  .contacts li { display: flex; align-items: center; justify-content: flex-end; gap: 6px; }
  .contacts svg { width: 11px; height: 11px; }

  .person {
    position: absolute;
    left: 30px;
    bottom: 18px;
    color: var(--paper);
  }
  .person-name { font-size: 17px; font-weight: 600; line-height: 1.2; }
  .person-title { font-size: 13px; margin-top: 2px; }

  .card-back .brand { top: 80px; color: var(--paper); }
  .card-back .brand-name { font-size: 46px; }
  .card-back .brand-dot { width: 15px; height: 15px; background: var(--paper); }
  .card-back .brand-slogan { margin-top: 12px; font-size: 14px; }
  .back-web {
    position: absolute;
    left: 0;
    right: 0;
    bottom: 42px;
    text-align: center;
    font-size: 24px;
    letter-spacing: 0.18em;
    color: var(--paper);
  }
</style>
</head>
<body>
<main class="canvas">

  <section class="card card-front" aria-label="Card front">
    <div class="brand">
      <div class="brand-name"><span>KERNELWORKS</span><span class="brand-dot"></span></div>
      <div class="brand-slogan">Technology Made Clear</div>
    </div>

    <p class="address">00, Complex name, City, State 0042</p>

    <ul class="contacts">
      <li>
        <svg viewBox="0 0 12 12"><path d="M2,1 L4.5,1 L5.5,3.5 L4,4.6 C4.7,6 6,7.3 7.4,8 L8.5,6.5 L11,7.5 L11,10 C6,10.5 1.5,6 2,1 Z" fill="var(--ink)"/></svg>
        <span>0123 456789</span>
      </li>
      <li>
        <svg viewBox="0 0 12 12"><rect x="1" y="5" width="10" height="6" rx="1" fill="var(--ink)"/><rect x="3" y="1" width="6" height="4" fill="var(--ink)"/></svg>
        <span>0123 456789</span>
      </li>
      <li>
        <svg viewBox="0 0 12 12"><rect x="1" y="2.5" width="10" height="7" rx="1" fill="var(--ink)"/><path d="M1.5,3 L6,6.5 L10.5,3" stroke="var(--paper)" fill="none"/></svg>
        <span>info@kernelworks.com</span>
      </li>
      <li>
        <svg viewBox="0 0 12 12"><circle cx="6" cy="6" r="5" fill="var(--ink)"/><path d="M1,6 H11 M6,1 C3,4 3,8 6,11 M6,1 C9,4 9,8 6,11" stroke="var(--paper)" stroke-width="0.8" fill="none"/></svg>
        <span>www.kernelworks.com</span>
      </li>
    </ul>

    <div class="front-band" role="img" aria-label="Decorative band in olive, lime and charcoal"></div>

    <div class="person">
      <div class="person-name">Your Name</div>
      <div class="person-title">Title</div>
    </div>
  </section>

  <section class="card card-back" aria-label="Card back">
    <div class="brand">
      <div class="brand-name"><span>KERNELWORKS</span><span class="brand-dot"></span></div>
      <div class="brand-slogan">Technology Made Clear</div>
    </div>
    <div class="back-web">www.kernelworks.com</div>
  </section>

</main>
</body>
</html>
```